Lantern & Pines Festival poster,rack card, business card

We need phase 1 of the 1st annual Lantern & Pines Festival to be held June 12 &13 2015. Location and etc to be given upon completion. We need a Poster design for store windows, a rack card for rack display, and a business size card to hand out to prospective exhibitors and attendees. The festival will focus on Food trucks and food vendors, along with multiple bands to play throughout the event . Additional work will be asked for after the phase one is complete, and we have more info such as sponsors and bands.

Attn all designers...... I opologize for the extreme delay on the project. I had an incendent that landed me in the hospital on sept 7, and I will not be released until next week ,at which time we will come to a decision. Thanks for your patience. Milo

```html
<!DOCTYPE html>
<html lang="en">
<head>
<meta charset="utf-8">
<title>Lantern &amp; Pines Festival – Rack Card</title>
<link href="https://fonts.googleapis.com/css2?family=Jost:wght@400;600;700&family=Yellowtail&display=swap" rel="stylesheet">
<style>
  :root {
    --page: #e9e6e1;
    --mint: #a9ddd0;
    --mint-light: #d6efe8;
    --mint-pale: #e4f4ef;
    --ink: #1d1f22;
    --charcoal: #2c2f33;
    --red: #d2533f;
    --orange: #f7b02b;
    --white: #ffffff;
  }
  * { box-sizing: border-box; margin: 0; padding: 0; }
  html, body {
    width: 872px; height: 1200px; overflow: hidden;
    background: var(--page);
  }
  .rack-card {
    position: absolute; left: 156px; top: 40px;
    width: 560px; height: 1120px; overflow: hidden;
    background: radial-gradient(ellipse at 50% 20%, var(--mint-light) 0%, var(--mint) 70%);
    font-family: "Jost", "Futura", sans-serif;
    color: var(--ink);
  }
  .festival-mark {
    position: absolute; left: 50%; top: 62px; transform: translateX(-50%);
    width: 290px; height: 290px;
    display: flex; align-items: center; justify-content: center;
  }
  .festival-mark__disc {
    position: absolute; inset: 0; border-radius: 50%;
    background: var(--orange);
  }
  .festival-mark__name {
    position: relative; text-align: center;
    font-weight: 700; font-size: 38px; line-height: 1.1;
    color: var(--charcoal); text-transform: uppercase; letter-spacing: 1px;
  }
  .street-scene {
    position: absolute; left: 0; top: 370px; width: 100%; height: 155px;
    background: linear-gradient(180deg, rgba(44,47,51,0) 0%, rgba(44,47,51,0.55) 45%, var(--charcoal) 100%);
  }
  .details {
    position: absolute; left: 0; top: 525px; width: 100%; height: 595px;
    background: var(--mint-pale);
  }
  .tagline {
    position: absolute; top: 40px; width: 100%; text-align: center;
    font-weight: 400; font-size: 25px; letter-spacing: 0.5px; text-transform: uppercase;
  }
  .address {
    position: absolute; top: 74px; width: 100%; text-align: center;
    font-weight: 700; font-size: 28px; line-height: 1.15; text-transform: uppercase;
  }
  .ribbon {
    position: absolute; left: 50%; transform: translateX(-50%);
    display: flex; align-items: center; justify-content: center;
    padding: 0 40px; white-space: nowrap;
    text-transform: uppercase; color: var(--white); font-weight: 700;
    clip-path: polygon(0 0, 100% 0, 96% 50%, 100% 100%, 0 100%, 4% 50%);
  }
  .ribbon--date {
    top: 173px; width: 520px; height: 48px;
    background: var(--red); font-size: 27px;
  }
  .ribbon--tickets {
    top: 430px; width: 520px; height: 44px;
    background: var(--orange); font-size: 17px; letter-spacing: 0;
  }
  .beer-partner {
    position: absolute; top: 262px; width: 100%; text-align: center;
    font-weight: 700; font-size: 29px; line-height: 1.2; text-transform: uppercase;
  }
  .slogan {
    position: absolute; top: 352px; width: 100%; text-align: center;
    font-family: "Yellowtail", "Brush Script MT", cursive; font-size: 46px;
  }
  .sponsors {
    position: absolute; top: 500px; left: 30px; right: 30px;
  }
  .sponsors__title {
    display: flex; align-items: center; gap: 12px;
    font-family: "Yellowtail", "Brush Script MT", cursive; font-size: 24px;
  }
  .sponsors__title::before, .sponsors__title::after {
    content: ""; flex: 1; height: 2px; background: var(--ink);
  }
  .sponsors__slots {
    display: flex; justify-content: space-between; margin-top: 12px;
  }
  .sponsor-slot {
    width: 80px; height: 28px; background: var(--white);
  }
</style>
</head>
<body>
  <main class="rack-card">
    <div class="festival-mark">
      <span class="festival-mark__disc"></span>
      <p class="festival-mark__name">Lantern &amp; Pines<br>Festival</p>
    </div>

    <div class="street-scene" role="img" aria-label="Silhouette of a food truck and a city skyline with a guitar headstock"></div>

    <section class="details">
      <p class="tagline">Outdoor Food &amp; Music Festival</p>
      <p class="address">418 Harbor Lane,<br>Maple Falls, Ohio</p>
      <p class="ribbon ribbon--date">June 12 &amp; 13, 2015</p>
      <p class="beer-partner">Copperline &amp; The Tall Oak<br>Beer Truck</p>
      <p class="slogan">Great Food &amp; Live Music</p>
      <p class="ribbon ribbon--tickets">Tickets available at lanternpinesfest.com</p>
      <div class="sponsors">
        <p class="sponsors__title">Sponsors</p>
        <div class="sponsors__slots">
          <span class="sponsor-slot"></span>
          <span class="sponsor-slot"></span>
          <span class="sponsor-slot"></span>
          <span class="sponsor-slot"></span>
          <span class="sponsor-slot"></span>
        </div>
      </div>
    </section>
  </main>
</body>
</html>
```